New web/graphic designs required to improve existing ecommerce site.

Initial outline of project:
This project is for new designs to fit into areas of existing webpages - specifically:-
Objective 1 - Produce 8 home page design proposals (design for central area of page only, not whole page)
Objective 2 - Produce 5 designs for page header banners (950px x 84px images)
Objective 3 - Produce 10 designs for help guide covers (316px x 410px images)
Also, on a more general note:
Objective 4 - Review and suggest improvements for other areas website. (This may lead to further design work)
-
Introduction to the Periodical Bazaar website:
The Periodical Bazaar website is a marketplace where back-issue hobby magazines can be bought and sold, and in some cases downloaded & viewed in digital form. The ‘sellers’ of the magazines will be both traders and private individuals. Trade sellers will also be able to sell magazine subscriptions and have ‘Promotion Pages’ about themselves and/or their magazine titles on the site. Other forms of advertising will also be available on the site for any commercial advertisers who want it, particularly for companies supplying the various hobbies covered.
Users of the website can locate magazines of interest to them by browsing through the hobby / category sections of the site, or by doing keyword searches for issues containing articles on specific topics.
The site is split-up into sections dealing with magazines about specific hobby subjects – ie., cars, motorbikes, railway, aviation, boating etc. Although part of the larger site, each of these sections is largely self-contained, with many users only ever browsing in the section related to their hobby. As such, each section effectively has it’s own home page, which will duplicate much of the information shown on the main home page. These multiple ‘section home pages’ will be promoted in their own right via URLs specific to that hobby. Currently there are 8 sections, but this number is expected to increase as the site grows.
This website is still being developed, but is close to launch; as such the website is fully functional but a lot of content is missing - please bear this in mind when viewing the site, and feel free to ask for clarification if anything is unclear.
The new website is currently at: http://www2.periodicalbazaar.co.uk
This website will replace several existing sites:-
http://www.periodicalbazaar.co.uk
http://www.twowheel-journals.co.uk
http://www.skyward-journals.co.uk
http://www.drivepapers.co.uk
http://www.trackside-journals.co.uk
http://www.scalecraft-journals.co.uk
-
Design notes:
The overall design is fairly conventional and very much ‘functionality’ driven, the website being at it’s heart an ecommerce system with some fairly complex features. Nevertheless I want the site to appear simple and modern in appearance, being somewhere between an ‘all style’ Web 2.0-type site (eg. tintly.io), and an ‘all function’ conventional trading site (eg. Bravlo, Quibb etc). A good example of a style of site which I would like to emulate is PostGecko – a complex and large site made to look friendly and approachable by the use of simple, clear design, bold colour and a sense of humour.
To explain further what is required I have prepared various image documents which include more detailed notes on the various objectives for this project. There is a lot of information in these documents - please read them carefully:-
Objective 1:
- Produce 1 'Main Home Page' design proposal
- Produce 8 'Section Home Page' design proposals - one each for these sections: Railway, Boating, Aviation, Cycling, Automotive, Motorcycling, Men's Lifestyle, Modelling
More information on Objective 1 is given in these image documents:
http://www.filenook.net/Home_Page_Designs-Purpose.gif
http://www.filenook.net/Home_Page_Designs-Areas.gif
http://www.filenook.net/Section_Home_Pages-1.gif
http://www.filenook.net/Section_Home_Pages-2.gif
-
Objective 2:
- Produce 5 designs for page header banners (950px x 84px images)
More information on Objective 2 is given in this image document:
http://www.filenook.net/Page_Header_Banners.gif
-
Objective 3:
- Produce 10 designs for help guide covers (316px x 410px images)
http://www.filenook.net/Help_Guide_Covers.gif
-
Objective 4:
- Review and suggest improvements for other areas website
I would like the designer to spend some time looking at the whole of the current website, and suggest any areas that can be improved. I am not looking for a wholesale re-design - the overall layout of the site and major design elements such as the navigation system - are essentially fixed - however, many graphical elements can be changed, as can any text content (including text content within the navigation system).
Improvements which are suggested may lead to additional design work either as part of this project, or as subsequent projects in their own right.
-
Designers are very welcome to contact me to discuss any aspect of this project, or if more information is required about the website or the designs required.
I'm happy to guarantee this project in due course, if there is positive reaction to the project from potential designers interested in submitting designs. This is the second project I have run on ArtBrigade - the first one was successful and resulted in the Flash animation that is currently on the homepage of the website.
UPDATE 11/10/11:
I've created some new documents to illustrate the sort of designs I am looking for for the Main Home Page and Section Home Pages:
Very rough examples of the sort of style I am looking for:
http://www.filenook.net/Rough_Main_Home_Page_1.jpg
http://www.filenook.net/Rough_Main_Home_Page_2.jpg
http://www.filenook.net/Rough_Main_Home_Page_3.jpg
http://www.filenook.net/Rough_Main_Home_Page_4.jpg
http://www.filenook.net/Rough_Main_Home_Page_5.jpg
http://www.filenook.net/Rough_Section_Home_Page.jpg
http://www.filenook.net/Rough_Section_Home_Page_2.jpg
Detailed document showing exact content required for the Main Home Page and each Section Home Page:
http://www.filenook.net/Home_Page_Content.gif
Target Market(s)
Mainly male, age 20 - 60. Not necessarily 'web savvy' or design-conscious
Industry/Entity Type
Advertising
Look and feel

```html
<!DOCTYPE html>
<html lang="en">
<head>
<meta charset="utf-8">
<title>Periodical Bazaar – Help Guide Covers</title>
<link rel="stylesheet" href="https://fonts.googleapis.com/css2?family=Mulish:wght@400;800&display=swap">
<style>
  :root {
    --canvas: #ffffff;
    --card-border: #3a3a3a;
    --band: #ffffff;
    --ink: #3b3b3b;
    --bubble-ink: #4a4a4a;
    --account: #e4a173;
    --selling: #c96b7d;
    --searching: #74b3c3;
    --buying-back: #c3ad73;
    --who: #e3dc82;
    --subscriptions: #9dbd6d;
    --legal: #a6da79;
    --advertising: #6ea0df;
    --digital: #7c8dcc;
    --trade: #8b75c8;
    --figure-top: #a9c4dc;
    --figure-bottom: #2f63b3;
  }
  * { box-sizing: border-box; margin: 0; padding: 0; }
  html, body {
    width: 1200px; height: 900px; overflow: hidden;
    background: var(--canvas);
    font-family: "Mulish", "Century Gothic", sans-serif;
  }
  .cover-set { position: relative; width: 1200px; height: 900px; }

  .cover {
    position: absolute;
    width: 193px; height: 252px;
    border: 2px solid var(--card-border);
    border-radius: 15px;
    overflow: hidden;
    background: linear-gradient(160deg, color-mix(in srgb, var(--tone) 88%, #fff) 0%, var(--tone) 55%, color-mix(in srgb, var(--tone) 90%, #000) 100%);
    box-shadow: 3px 4px 6px rgba(0,0,0,0.35);
  }
  .row-1 { top: 173px; }
  .row-2 { top: 445px; }
  .col-1 { left: 72px; }
  .col-2 { left: 292px; }
  .col-3 { left: 507px; }
  .col-4 { left: 723px; }
  .col-5 { left: 943px; }

  .cover-title {
    position: absolute;
    left: 0; top: 35px;
    width: 182px; height: 46px;
    background: var(--band);
    border-radius: 0 5px 5px 0;
    display: flex; flex-direction: column; justify-content: center; align-items: center;
    color: var(--ink);
    line-height: 1.08;
    text-align: center;
  }
  .title-main {
    font-weight: 800; font-size: 17px; letter-spacing: 2px; text-transform: uppercase;
  }
  .title-sub { font-weight: 400; font-size: 17px; }

  .welcome-bubble {
    position: absolute;
    left: 72px; top: 122px;
    width: 94px; height: 52px;
    background: var(--band);
    border-radius: 50%;
    display: flex; align-items: center; justify-content: center;
    text-align: center;
    font-size: 6.5px; line-height: 1.35;
    color: var(--bubble-ink);
    text-transform: uppercase;
  }
  .welcome-bubble::after {
    content: "";
    position: absolute;
    left: 16px; bottom: -10px;
    width: 16px; height: 16px;
    background: var(--band);
    clip-path: polygon(30% 0, 100% 0, 0 100%);
  }

  .mascot {
    position: absolute;
    left: 0; top: 132px;
    width: 82px; height: 118px;
    border-radius: 30px 30px 8px 8px;
    background: linear-gradient(180deg, var(--figure-top) 0%, #e8c7a4 30%, var(--figure-bottom) 65%, #3d4a5c 100%);
    opacity: 0.9;
  }
</style>
</head>
<body>
<main class="cover-set">

  <section class="cover row-1 col-1" style="--tone: var(--account)">
    <h2 class="cover-title"><span class="title-main">Managing</span><span class="title-sub">your account</span></h2>
    <div class="mascot" role="img" aria-label="Cartoon mascot in cap and blue overalls waving"></div>
    <p class="welcome-bubble">Welcome to<br>Periodical Bazaar<br>help guide</p>
  </section>

  <section class="cover row-1 col-2" style="--tone: var(--selling)">
    <h2 class="cover-title"><span class="title-main">Selling</span><span class="title-sub">back issues</span></h2>
    <div class="mascot" role="img" aria-label="Cartoon mascot in cap and blue overalls waving"></div>
    <p class="welcome-bubble">Welcome to<br>Periodical Bazaar<br>help guide</p>
  </section>

  <section class="cover row-1 col-3" style="--tone: var(--searching)">
    <h2 class="cover-title"><span class="title-main">Searching &amp;</span><span class="title-sub">browseing</span></h2>
    <div class="mascot" role="img" aria-label="Cartoon mascot in cap and blue overalls waving"></div>
    <p class="welcome-bubble">Welcome to<br>Periodical Bazaar<br>help guide</p>
  </section>

  <section class="cover row-1 col-4" style="--tone: var(--buying-back)">
    <h2 class="cover-title"><span class="title-main">Buying</span><span class="title-sub">back issues</span></h2>
    <div class="mascot" role="img" aria-label="Cartoon mascot in cap and blue overalls waving"></div>
    <p class="welcome-bubble">Welcome to<br>Periodical Bazaar<br>help guide</p>
  </section>

  <section class="cover row-1 col-5" style="--tone: var(--who)">
    <h2 class="cover-title"><span class="title-main">Who we are</span></h2>
    <div class="mascot" role="img" aria-label="Cartoon mascot in cap and blue overalls waving"></div>
    <p class="welcome-bubble">Welcome to<br>Periodical Bazaar<br>help guide</p>
  </section>

  <section class="cover row-2 col-1" style="--tone: var(--subscriptions)">
    <h2 class="cover-title"><span class="title-main">Buying</span><span class="title-sub">subscriptions</span></h2>
    <div class="mascot" role="img" aria-label="Cartoon mascot in cap and blue overalls waving"></div>
    <p class="welcome-bubble">Welcome to<br>Periodical Bazaar<br>help guide</p>
  </section>

  <section class="cover row-2 col-2" style="--tone: var(--legal)">
    <h2 class="cover-title"><span class="title-main">Legal stuff</span></h2>
    <div class="mascot" role="img" aria-label="Cartoon mascot in cap and blue overalls waving"></div>
    <p class="welcome-bubble">Welcome to<br>Periodical Bazaar<br>help guide</p>
  </section>

  <section class="cover row-2 col-3" style="--tone: var(--advertising)">
    <h2 class="cover-title"><span class="title-main">Advertising</span><span class="title-sub">information &amp; rates</span></h2>
    <div class="mascot" role="img" aria-label="Cartoon mascot in cap and blue overalls waving"></div>
    <p class="welcome-bubble">Welcome to<br>Periodical Bazaar<br>help guide</p>
  </section>

  <section class="cover row-2 col-4" style="--tone: var(--digital)">
    <h2 class="cover-title"><span class="title-main">Buying</span><span class="title-sub">digital editions</span></h2>
    <div class="mascot" role="img" aria-label="Cartoon mascot in cap and blue overalls waving"></div>
    <p class="welcome-bubble">Welcome to<br>Periodical Bazaar<br>help guide</p>
  </section>

  <section class="cover row-2 col-5" style="--tone: var(--trade)">
    <h2 class="cover-title"><span class="title-main">Trade</span><span class="title-main">services</span></h2>
    <div class="mascot" role="img" aria-label="Cartoon mascot in cap and blue overalls waving"></div>
    <p class="welcome-bubble">Welcome to<br>Periodical Bazaar<br>help guide</p>
  </section>

</main>
</body>
</html>
```